web page design with coding

We are a start up insurance agency who needs to design a full functional web page. we recently did a postcard design though drawkettle I will upload the final project for you to see the color scheme/font we would like to continue to use. I also have a rough draft of verbage I would like our website to have. I will upload that as well.

Reason: I am sorry but the person who will make the final decision on the website is out of the country at the moment and will make the final decision when he returns.

Industry/Entity Type

Insurance

Coding

Coded - Design and coding required

```html
<!DOCTYPE html>
<html lang="en">
<head>
<meta charset="utf-8">
<title>Veritas Cover Group</title>
<link rel="stylesheet" href="https://fonts.googleapis.com/css2?family=Lato:wght@400;700&family=Open+Sans:ital,wght@0,400;0,600;1,400&display=swap">
<style>
:root{
  --green:#2e7d3e;
  --navy:#1d3a6b;
  --slate:#5f6f96;
  --ink:#3c3c3c;
  --muted:#666;
  --soft:#f6f6f6;
  --card:#ececec;
  --footer:#2b2b2b;
  --white:#fff;
}
*{margin:0;padding:0;box-sizing:border-box}
html,body{width:706px;height:1200px;overflow:hidden;background:var(--white)}
body{position:relative;font-family:"Open Sans",Arial,sans-serif;color:var(--ink)}
.abs{position:absolute}
.top-rule{left:0;top:0;width:706px;height:3px;background:var(--green)}
.brand{left:56px;top:14px;color:var(--navy);font-family:"Lato",sans-serif;font-weight:700;text-align:center;line-height:1}
.brand .mark{font-size:32px;letter-spacing:1px}
.brand .name{font-size:11px;margin-top:5px}
.phone{left:566px;top:20px;display:flex;align-items:center;gap:7px;font-size:8.5px;color:#222}
.nav{top:47px;left:0;width:706px;font-size:7.2px;text-transform:uppercase}
.nav a{position:absolute;color:#333;text-decoration:none;white-space:nowrap}
.nav a.active{color:var(--green)}
.hero{left:0;top:70px;width:706px;height:370px;overflow:hidden}
.hero-photo{position:absolute;inset:0;background:linear-gradient(100deg,#c9b07a 0%,#d9c79c 30%,#a9b070 60%,#6e8a3c 85%,#4f6a2a 100%)}
.hero-curve{position:absolute;left:0;top:0}
.hero-copy{left:432px;top:156px;color:var(--white);width:220px}
.hero-copy h2{font-family:"Lato",sans-serif;font-weight:700;font-size:15.5px}
.hero-copy p{font-size:7.4px;line-height:15px;margin-top:2px}
.btn-read{display:inline-block;margin-top:7px;width:74px;height:26px;line-height:26px;text-align:center;background:var(--green);color:var(--white);font-size:7.2px;font-weight:600}
.arrow{top:170px;width:10px;height:32px}
.welcome{left:0;top:458px;width:706px;text-align:center}
.welcome h1{font-family:"Lato",sans-serif;font-weight:700;font-size:19px;color:#444}
.welcome h1 span,.coverage h2 span{color:var(--navy)}
.welcome p{width:520px;margin:11px auto 0;font-size:6.7px;line-height:15px;color:#555}
.card{top:536px;width:270px;height:192px;background:var(--card)}
.card .photo{height:146px}
.card h3{font-family:"Lato",sans-serif;font-weight:700;font-size:11.5px;text-align:center;margin-top:10px;color:#333}
.card small{display:block;text-align:center;font-style:italic;font-size:5.8px;color:#888;margin-top:1px}
.coverage{left:0;top:760px;width:706px;height:240px;background:var(--soft);border-top:1px solid #ececec}
.coverage h2{position:absolute;top:34px;width:100%;text-align:center;font-family:"Lato",sans-serif;font-weight:700;font-size:18.5px;color:#444}
.coverage .sub{position:absolute;top:64px;width:100%;text-align:center;font-style:italic;font-size:6.5px;color:#555}
.service{top:100px;width:140px;text-align:center}
.service .icon{width:56px;height:56px;border-radius:50%;margin:0 auto;display:flex;align-items:center;justify-content:center;background:var(--slate)}
.service .icon.primary{background:var(--green)}
.service h4{font-size:7.8px;font-weight:600;margin-top:11px;color:#222;line-height:11px}
.service p{font-size:6.8px;color:#555;line-height:11px;margin-top:1px}
.newsletter{left:0;top:1000px;width:706px;height:38px;background:var(--green)}
.nl-icon{left:60px;top:6px;width:27px;height:27px;border:1.5px solid var(--white);border-radius:50%;display:flex;align-items:center;justify-content:center}
.nl-label{left:103px;top:11px;font-size:11px;color:var(--white)}
.field{top:9px;height:22px;background:var(--white);font-size:7.3px;color:#888;padding:6px 9px}
.btn-login{left:578px;top:9px;width:72px;height:22px;background:var(--navy);color:var(--white);font-size:7.3px;text-align:center;line-height:22px}
.footer{left:0;top:1038px;width:706px;height:132px;background:var(--footer);color:#ddd}
.footer .brand{left:56px;top:46px;color:var(--white)}
.col{top:22px;font-size:6.7px;line-height:12px}
.col h5{font-family:"Lato",sans-serif;font-weight:700;font-size:8.6px;color:var(--white);margin-bottom:6px;letter-spacing:.2px}
.col .row{display:flex;align-items:center;gap:5px;margin-top:3.5px}
.social .row{margin-top:5px;margin-bottom:3px}
.social .sq{width:14px;height:14px;border:1px solid #bbb}
.legal{left:0;top:1170px;width:706px;height:30px;background:linear-gradient(#2c568c,#1d3a6b);color:#dfe6f2;font-size:6.8px;text-align:center;line-height:30px}
</style>
</head>
<body>
<div class="abs top-rule"></div>

<header>
  <div class="abs brand"><div class="mark">VCG</div><div class="name">Veritas Cover Group</div></div>
  <div class="abs phone">
    <svg width="15" height="15" viewBox="0 0 16 16"><circle cx="8" cy="8" r="7" fill="none" stroke="#2e7d3e" stroke-width="1.2"/><path d="M5.6 4.6l1.3-.3.8 1.9-.9.7a5 5 0 0 0 2.3 2.3l.7-.9 1.9.8-.3 1.3c-3.3.2-6-2.5-5.8-5.8z" fill="#2e7d3e"/></svg>
    <span>(555)-010 274</span>
  </div>
  <nav class="abs nav">
    <a class="active" style="left:328px">Home</a>
    <a style="left:373px">About Us</a>
    <a style="left:431px">Services</a>
    <a style="left:486px">Blog</a>
    <a style="left:528px">Testimonials</a>
    <a style="left:602px">Contact Us</a>
  </nav>
</header>

<section class="abs hero">
  <div class="hero-photo" role="img" aria-label="Photo of a happy family of four playing together outdoors in a sunny park"></div>
  <svg class="hero-curve" width="706" height="370" viewBox="0 0 706 370">
    <path d="M0 300 C150 370 420 370 706 232 L706 370 L0 370 Z" fill="#1d3a6b"/>
    <path d="M0 294 C140 352 390 352 706 230 L706 370 L0 370 Z" fill="#2e7d3e"/>
    <path d="M0 318 C170 376 440 378 706 250 L706 370 L0 370 Z" fill="#1d3a6b"/>
    <path d="M0 322 C170 372 440 374 706 260 L706 370 L0 370 Z" fill="#ffffff"/>
  </svg>
  <svg class="abs arrow" style="left:20px" viewBox="0 0 10 32"><path d="M9 1L1 16l8 15" fill="none" stroke="#fff" stroke-width="1" opacity=".7"/></svg>
  <svg class="abs arrow" style="left:676px" viewBox="0 0 10 32"><path d="M1 1l8 15-8 15" fill="none" stroke="#fff" stroke-width="1" opacity=".7"/></svg>
  <div class="abs hero-copy">
    <h2>Personal Umbrella Insurance</h2>
    <p>Veritas Cover Group has joined with regional &amp; national insurance companies to provide quality</p>
    <span class="btn-read">Read More</span>
  </div>
</section>

<section class="abs welcome">
  <h1>WELCOME TO <span>VERITAS COVER GROUP</span></h1>
  <p>Established in 2015, Veritas Cover Group is a full service independent insurance agency. Our licensed agents have the experience to custom tailor a program to meet your specific needs &amp; our professional support staff will provide you with top notch customer service</p>
</section>

<a class="abs card" style="left:74px">
  <div class="photo" role="img" aria-label="Photo of a business meeting with a handshake between clients and an agent" style="background:linear-gradient(110deg,#e7e9ec,#c9ccd2 45%,#3a4252 85%)"></div>
  <h3>BUSINESS INSURANCE</h3><small>Click here for view information</small>
</a>
<a class="abs card" style="left:369px">
  <div class="photo" role="img" aria-label="Photo of parents smiling at their toddler in a car seat" style="background:linear-gradient(110deg,#d9c2a8,#e9a070 45%,#c8b4a2 70%,#8a3a3a 100%)"></div>
  <h3>PERSONAL INSURANCE</h3><small>Click here for view information</small>
</a>

<section class="abs coverage">
  <h2>BUSINESS <span>INSURANCE COVERAGE</span></h2>
  <div class="sub">Veritas Cover Group provides</div>
  <div class="abs service" style="left:58px">
    <div class="icon primary"><svg width="18" height="16" viewBox="0 0 18 16"><rect x="6" y="1" width="6" height="3" fill="none" stroke="#fff" stroke-width="1.6"/><rect x="1" y="4" width="16" height="11" rx="1" fill="#fff"/><rect x="1" y="8.5" width="16" height="1.2" fill="#2e7d3e"/></svg></div>
    <h4>BUSINESS OWNERS<br>POLICY (BOP)</h4><p>Business insurance is a risk man agement tool that enables</p>
  </div>
  <div class="abs service" style="left:206px">
    <div class="icon"><svg width="20" height="15" viewBox="0 0 20 15"><rect x="1" y="1" width="11" height="9" fill="#fff"/><path d="M12 4h4l3 3v3h-7z" fill="#fff"/><circle cx="5" cy="12" r="2" fill="#fff"/><circle cx="15" cy="12" r="2" fill="#fff"/></svg></div>
    <h4>COMMERCIAL AUTO</h4><p>Business insurance is a risk man agement tool that enables</p>
  </div>
  <div class="abs service" style="left:354px">
    <div class="icon"><svg width="16" height="17" viewBox="0 0 16 17"><circle cx="8" cy="5" r="4" fill="#fff"/><path d="M1 17c0-5 3-7 7-7s7 2 7 7z" fill="#fff"/></svg></div>
    <h4>DIRECTORS AND OFFICERS<br>(D&amp;O)</h4><p>Business insurance is a risk man agement tool that enables</p>
  </div>
  <div class="abs service" style="left:496px">
    <div class="icon"><svg width="16" height="16" viewBox="0 0 16 16" fill="#fff"><path d="M1 1h5L1 6zM15 1v5l-5-5zM1 15v-5l5 5zM15 15h-5l5-5z"/><path d="M3 3l10 10M13 3L3 13" stroke="#fff" stroke-width="2"/></svg></div>
    <h4>DIFFERENCE IN CONDITIONS</h4><p>Business insurance is a risk man agement tool that enables</p>
  </div>
</section>

<section class="abs newsletter">
  <div class="abs nl-icon"><svg width="12" height="9" viewBox="0 0 12 9"><rect width="12" height="9" rx="1" fill="#fff"/><path d="M0.5 1l5.5 4 5.5-4" fill="none" stroke="#2e7d3e" stroke-width="1.1"/></svg></div>
  <div class="abs nl-label">Newsletter</div>
  <svg class="abs" style="left:180px;top:9px" width="8" height="20" viewBox="0 0 8 20"><path d="M1 1l6 9-6 9" fill="none" stroke="#7fb88a" stroke-width="1"/></svg>
  <div class="abs field" style="left:206px;width:172px">Enter your name...</div>
  <div class="abs field" style="left:389px;width:171px">Enter your email address...</div>
  <div class="abs btn-login">Login</div>
</section>

<footer class="abs footer">
  <div class="abs brand"><div class="mark">VCG</div><div class="name">Veritas Cover Group</div></div>
  <div class="abs col" style="left:220px">
    <h5>QUICK LINKS</h5>
    <div>Home</div><div>About Us</div><div>Services</div><div>Blog</div><div>Testimonials</div><div>Contact Us</div>
  </div>
  <div class="abs col" style="left:329px">
    <h5>CONTACT</h5>
    <div>1820 Harbor Lane, Suite 140</div><div>Bayview, FL 30100</div>
    <div class="row"><svg width="5" height="8" viewBox="0 0 5 8"><rect x=".5" y=".5" width="4" height="7" rx=".8" fill="none" stroke="#ddd"/></svg>(555) - 010 274</div>
    <div class="row"><svg width="7" height="6" viewBox="0 0 7 6"><rect y="2" width="7" height="4" fill="#ddd"/><rect x="1.5" width="4" height="2" fill="#ddd"/></svg>(555) 013-4417</div>
    <div class="row"><svg width="7" height="5" viewBox="0 0 7 5"><rect width="7" height="5" fill="#ddd"/><path d="M0 0l3.5 2.8L7 0" fill="none" stroke="#2b2b2b" stroke-width=".8"/></svg>hello@vcgcover.com</div>
  </div>
  <div class="abs col" style="left:471px">
    <h5>INFORMATION</h5>
    <div>Privacy Policy</div><div>Terms &amp; Conditions</div><div>Sitemap</div>
  </div>
  <div class="abs col social" style="left:582px">
    <h5>FOLLOW US</h5>
    <div class="row"><span class="sq"></span>: Community</div>
    <div class="row"><span class="sq"></span>: Updates</div>
    <div class="row"><span class="sq"></span>: Network</div>
    <div class="row"><span class="sq"></span>: Circles</div>
  </div>
</footer>

<div class="abs legal">Copyrights ©vcg 2016. All rights reserved.</div>
</body>
</html>
```